Soy Candle Labels

We sell soy candles in recycled wine bottles. The wine bottle is cut in half and filled with pure and natural soy wax and scented with essential oils.
Our product represents good use of up cycling materials for a better use. The product is all natural and eco friendly.
You can see good use of labels and branding for a company in America that does the same thing http://larkmeadow7wicks.example/
Trya dn keep the label uncomplicated like the above labels.
We will need an area to hand stamp the scent. Similar to the labels used on the above website.
We would prefer to use a white or off white paper label with gold or bronze printing - limit the use of colour and keep the label simple and sophisticated.
Emberlace Candle Co. is our company name. Emberlace being the predominant name and candle co. written small underneath right justified.
Die cut labels might look better than a rectangle.
Dimensions should be 90mm Wide x 90mm High
The final design should communicate a professional and quality product. But stay modern and professional. Clean, elegant and sophisticated.
Can use wording such as: Hand Poured, Premium Soy Wax, All Natural, Up cycled
Have a look at the attached image for the look and feel we are going for.
Updates
Designers are having a little bit of trouble interpreting the brief into a viable design. To assist perhaps you can look at WINE LABELS on google images. Design your label around an existing style wine label to give the canld ethe feel of being a bottle of wine. Get creative! :)
Reason: We require more designs. We havnt quite got what were looking for.
Please see brief.

```html
<!DOCTYPE html>
<html lang="en">
<head>
<meta charset="utf-8">
<title>Emberlace Candle Co. – Soy Candle Label</title>
<link rel="stylesheet" href="https://fonts.googleapis.com/css2?family=Ropa+Sans&family=Pathway+Gothic+One&family=Open+Sans:wght@400&display=swap">
<style>
  :root {
    --gold: #a98832;
    --paper: #fffdf6;
    --bronze-ink: #3a1b10;
  }
  html, body {
    margin: 0;
    padding: 0;
    width: 1200px;
    height: 1000px;
    overflow: hidden;
    background: var(--gold);
  }
  .canvas {
    position: relative;
    width: 1200px;
    height: 1000px;
    background: var(--gold);
  }
  .label {
    position: absolute;
    left: 124px;
    top: 40px;
    width: 927px;
    height: 926px;
    background: var(--paper);
    color: var(--bronze-ink);
    overflow: hidden;
  }
  .label__band {
    position: absolute;
    left: 0;
    top: 0;
    width: 100%;
    height: 36px;
    background: var(--bronze-ink);
  }
  .claims {
    position: absolute;
    left: 47px;
    top: 66px;
    margin: 0;
    font-family: "Ropa Sans", sans-serif;
    line-height: 1;
  }
  .claims__title {
    display: block;
    font-size: 43px;
    margin-bottom: 10px;
  }
  .claims__line {
    display: block;
    font-size: 30px;
    margin-bottom: 8px;
  }
  .scent-stamp {
    position: absolute;
    right: 52px;
    top: 74px;
    width: 30px;
    font-family: "Ropa Sans", sans-serif;
    font-size: 31px;
    line-height: 34.5px;
    text-align: center;
    margin: 0;
  }
  .scent-stamp span { display: block; }
  .brand {
    position: absolute;
    right: 78px;
    top: 430px;
    text-align: right;
    margin: 0;
  }
  .brand__name {
    display: block;
    font-family: "Ropa Sans", sans-serif;
    font-size: 138px;
    line-height: 1;
    letter-spacing: 1px;
  }
  .brand__sub {
    display: block;
    font-family: "Open Sans", sans-serif;
    font-size: 29px;
    line-height: 1;
    margin-top: 12px;
  }
  .footer-note {
    position: absolute;
    bottom: 62px;
    margin: 0;
    font-family: "Pathway Gothic One", sans-serif;
    font-size: 50px;
    line-height: 1;
  }
  .footer-note--origin { left: 47px; }
  .footer-note--material { right: 45px; }
</style>
</head>
<body>
<main class="canvas">
  <section class="label" aria-label="Emberlace Candle Co. soy candle label">
    <div class="label__band"></div>

    <p class="claims">
      <span class="claims__title">Hand Poured</span>
      <span class="claims__line">All Natural Soy</span>
      <span class="claims__line">320 gm of Premium Soy Wax</span>
    </p>

    <p class="scent-stamp" aria-label="Scent">
      <span>S</span><span>C</span><span>E</span><span>N</span><span>T</span>
    </p>

    <h1 class="brand">
      <span class="brand__name">Emberlace</span>
      <span class="brand__sub">Candle Co.</span>
    </h1>

    <p class="footer-note footer-note--origin">Product of Australia</p>
    <p class="footer-note footer-note--material">Up-Cycled wine bottle</p>
  </section>
</main>
</body>
</html>
```